A Design Build Company Flyer Ad - Modern, clean [see website for sense of mood, loftquill.ca]

We are a Design Build Company . We need to create a full page advertisment that clearly conveys who we are (a design build firm) in a hockey tournament program. A subtle connecting tag line suitable to both our design/build services, and hockey could be wise, example:
- One Team One Dream
- With the right players, anything is possible

Please Note: There have been several submissions that visually attempted to connect hockey with construction, however I think it is a bit confusing- and think it would be best to keep it design/build and our brand consistant.

Please see our website: www.loftquill.ca for images, and further inspo on our style.

Target Market(s)

35-50 year olds - higher end real estate market

Industry/Entity Type

Construction: Design, Build

Requirements
Must have
• Our Logo (See attached) Images of work we have completed. (See website: www.loftquill.ca)

```html
<!DOCTYPE html>
<html lang="en">
<head>
<meta charset="utf-8">
<title>Loftquill Homes – One Team. One Dream.</title>
<link rel="stylesheet" href="https://fonts.googleapis.com/css2?family=Montserrat:wght@400;500;600;700&display=swap">
<style>
  :root {
    --ink: #1d1d1d;
    --band: #242424;
    --paper: #ffffff;
    --stage: #b7b7b7;
    --text: #2a2a2a;
    --rule: #3a3a3a;
  }
  * { margin: 0; padding: 0; box-sizing: border-box; }
  html, body { width: 1200px; height: 2164px; overflow: hidden; background: var(--stage); }
  body { font-family: "Montserrat", Arial, sans-serif; color: var(--text); position: relative; }

  .flyer {
    position: absolute; left: 50px; top: 394px;
    width: 1100px; height: 1375px;
    background: var(--paper); overflow: hidden;
    box-shadow: 0 10px 30px rgba(0,0,0,.18);
  }
  .flyer__band { position: absolute; left: 880px; top: 0; width: 220px; height: 100%; background: var(--band); }

  .brand { position: absolute; left: 41px; top: 41px; display: flex; align-items: center; gap: 26px; }
  .brand__ring { width: 200px; height: 200px; border-radius: 50%; border: 10px solid var(--ink); }
  .brand__name { font-weight: 700; font-size: 56px; color: var(--ink); letter-spacing: -.5px; }

  .headline {
    position: absolute; left: 38px; top: 356px;
    font-weight: 600; font-size: 100px; line-height: 93px; color: var(--ink); letter-spacing: -1px;
    white-space: nowrap;
  }

  .pill {
    position: absolute; height: 41px; padding: 0 20px;
    background: var(--ink); color: #fff; border-radius: 21px;
    font-weight: 500; font-size: 22px; line-height: 41px; white-space: nowrap; letter-spacing: .3px;
  }
  .pill--who { left: 41px; top: 583px; }
  .pill--services { left: 41px; top: 898px; }
  .pill--contact { left: 41px; top: 1139px; }
  .pill--assoc { left: 328px; top: 1139px; font-size: 20px; letter-spacing: .2px; padding: 0 19px; }

  .about { position: absolute; left: 41px; top: 650px; width: 620px; font-size: 17.5px; line-height: 23px; white-space: nowrap; }
  .about p + p { margin-top: 8px; }
  .about strong { font-weight: 500; color: var(--ink); }

  .rule { position: absolute; left: 41px; width: 620px; height: 1.5px; background: var(--rule); }
  .rule--one { top: 867px; }
  .rule--two { top: 1108px; }

  .services { position: absolute; left: 41px; top: 953px; list-style: none; font-size: 17.5px; }
  .services li { height: 34.5px; display: flex; align-items: center; gap: 8px; }
  .services svg, .contact svg { width: 13px; height: 13px; flex: none; }

  .divider { position: absolute; left: 282px; top: 1139px; width: 1.5px; height: 141px; background: var(--rule); }

  .contact { position: absolute; left: 41px; top: 1190px; list-style: none; font-size: 17.5px; font-weight: 500; }
  .contact li { height: 34.5px; display: flex; align-items: center; gap: 8px; white-space: nowrap; }
  .contact .phone { font-weight: 600; }

  .badge { position: absolute; background: #3a3a3a; }
  .badge--assoc { left: 330px; top: 1208px; width: 196px; height: 68px; border-radius: 8px; }
  .badge--mark { left: 553px; top: 1200px; width: 92px; height: 92px; border-radius: 50%; }

  .photo { position: absolute; left: 702px; width: 357px; height: 397px; background: #fff; padding: 7px; border: 2.5px solid var(--ink); box-shadow: 0 4px 10px rgba(0,0,0,.2); }
  .photo__fill { width: 100%; height: 100%; border-radius: inherit; }
  .photo--top { top: 41px; border-radius: 178px 178px 26px 26px; }
  .photo--mid { top: 489px; border-radius: 34px; }
  .photo--bottom { top: 936px; border-radius: 26px 26px 178px 178px; }
  .photo--top .photo__fill { background: linear-gradient(180deg, #c98a55 0%, #ece9e4 35%, #b98d63 70%, #a9a9a9 100%); }
  .photo--mid .photo__fill { background: linear-gradient(160deg, #f3f2ef 0%, #e6d0c8 45%, #e9e5df 70%, #3b4f6a 100%); }
  .photo--bottom .photo__fill { background: linear-gradient(180deg, #e8e8e6 0%, #8d8d8b 45%, #f2f2f0 65%, #3d3b3a 100%); }
</style>
</head>
<body>
  <main class="flyer">
    <div class="flyer__band"></div>

    <div class="brand">
      <div class="brand__ring"></div>
      <span class="brand__name">Loftquill</span>
    </div>

    <h1 class="headline">One Team.<br>One Dream.</h1>

    <div class="pill pill--who">Who We Are</div>
    <div class="about">
      <p><strong>Loftquill Homes Inc.</strong> is a design and renovation firm<br>based in <strong>Cedar Bay, British Columbia</strong>.</p>
      <p>Driven by its two main principles, Owen &amp; Marisa Kell,<br>the company provides services to the Harbour Shore, Cedar Bay, and<br>beyond. Services include interior design consulting and medium<br>renovations to full-scale home remodels.</p>
      <p>We are anchored by the belief that <strong>quality products</strong> and<br><strong>systems + quality service = a quality project and experience</strong>.</p>
    </div>
    <div class="rule rule--one"></div>

    <div class="pill pill--services">Our Services</div>
    <ul class="services">
      <li><svg viewBox="0 0 12 12"><circle cx="6" cy="6" r="4.5" fill="none" stroke="#2a2a2a"/><path d="M6 0v12M0 6h12" stroke="#2a2a2a"/></svg>Interior design</li>
      <li><svg viewBox="0 0 12 12"><circle cx="6" cy="6" r="4.5" fill="none" stroke="#2a2a2a"/><path d="M6 0v12M0 6h12" stroke="#2a2a2a"/></svg>Full scale home remodels to light renovations</li>
      <li><svg viewBox="0 0 12 12"><circle cx="6" cy="6" r="4.5" fill="none" stroke="#2a2a2a"/><path d="M6 0v12M0 6h12" stroke="#2a2a2a"/></svg>Custom build projects</li>
      <li><svg viewBox="0 0 12 12"><circle cx="6" cy="6" r="4.5" fill="none" stroke="#2a2a2a"/><path d="M6 0v12M0 6h12" stroke="#2a2a2a"/></svg>Carpentry services.</li>
    </ul>
    <div class="rule rule--two"></div>

    <div class="pill pill--contact">Contact Info</div>
    <div class="divider"></div>
    <ul class="contact">
      <li class="phone"><svg viewBox="0 0 12 12"><path d="M2 1l2 0 1 3-1.5 1a7 7 0 0 0 3.5 3.5L8 7l3 1v2a1 1 0 0 1-1 1A9 9 0 0 1 1 2a1 1 0 0 1 1-1z" fill="none" stroke="#2a2a2a"/></svg>604-555-0148</li>
      <li><svg viewBox="0 0 12 12"><rect x="1" y="2.5" width="10" height="7" fill="none" stroke="#2a2a2a"/><path d="M1 2.5l5 4 5-4" fill="none" stroke="#2a2a2a"/></svg>info@loftquill.ca</li>
      <li><svg viewBox="0 0 12 12"><circle cx="6" cy="6" r="5" fill="none" stroke="#2a2a2a"/><path d="M1 6h10M6 1c-3 3-3 7 0 10M6 1c3 3 3 7 0 10" fill="none" stroke="#2a2a2a"/></svg>www.loftquill.ca</li>
      <li><svg viewBox="0 0 12 12"><path d="M6 11S2 7 2 4.5a4 4 0 0 1 8 0C10 7 6 11 6 11z" fill="none" stroke="#2a2a2a"/><circle cx="6" cy="4.5" r="1.3" fill="#2a2a2a"/></svg>Alder Crescent, Cedar Bay, BC, Z4K, Canada</li>
    </ul>

    <div class="pill pill--assoc">Associations &amp; Certifications</div>
    <div class="badge badge--assoc" role="img" aria-label="Homebuilders association membership badge"></div>
    <div class="badge badge--mark" role="img" aria-label="Renovation certification badge"></div>

    <figure class="photo photo--top"><div class="photo__fill" role="img" aria-label="Open-plan living room and kitchen with wood beams and a modern chandelier"></div></figure>
    <figure class="photo photo--mid"><div class="photo__fill" role="img" aria-label="Bright sitting room with pink armchairs and a tufted ottoman"></div></figure>
    <figure class="photo photo--bottom"><div class="photo__fill" role="img" aria-label="Modern kitchen with white pendant lights and a dark island"></div></figure>
  </main>
</body>
</html>
```